Lawn care business card

I am looking for a quality designed personal business card to represent the quality and elegant nature of our company. We separate ourselves in our market by the aesthetic value of our work, so I am looking for marketing material that does the same. We target our marketing high end customers, and we try to avoid price shoppers. I am open to all design options, so long as they are in line with our companies values.

We are tend to go with a retro look on everything from our logo and print material, to our uniforms. We like to portray and "old fashion" set of core values, with a modern elegance. So a wild and crazy look is out of the question.

Things I'd like on the card:
1.) Logo
2.) Phone number: (816) 555-2931
3.) Website: Verdelynkc.com
4.) Email: robertfairley@verdelynkc.com
5.) My name: Robert Fairley
6.) Facebook link: neighborly.com/VerdelynGardenandGrounds
7.) Instagram: http://snapfolio.com/verdelynkc

Attached is a copy of our logo.

Reason: More time is needed to gather conclusive feedback from the members of our marketing team.

```html
<!DOCTYPE html>
<html lang="en">
<head>
<meta charset="utf-8">
<title>Verdelyn Business Card</title>
<link rel="stylesheet" href="https://fonts.googleapis.com/css2?family=Arimo:wght@400&display=swap">
<style>
  :root {
    --backdrop: #d9d6d3;
    --card: #ffffff;
    --ink: #141414;
    --accent: #e8431c;
  }
  html, body {
    margin: 0;
    padding: 0;
    width: 1200px;
    height: 960px;
    overflow: hidden;
    background: var(--backdrop);
    font-family: "Arimo", Arial, sans-serif;
    color: var(--ink);
  }
  .business-card {
    position: absolute;
    left: 150px;
    top: 223px;
    width: 900px;
    height: 514px;
    background: var(--card);
    box-shadow: 0 10px 30px rgba(0,0,0,0.25);
  }
  .brand-mark {
    position: absolute;
    left: 0;
    right: 0;
    top: 120px;
    display: flex;
    justify-content: center;
    align-items: center;
    gap: 16px;
  }
  .brand-dot {
    width: 64px;
    height: 64px;
    border-radius: 50%;
    background: var(--accent);
  }
  .brand-name {
    font-size: 46px;
    font-weight: 400;
    color: var(--ink);
    letter-spacing: 1px;
  }
  .divider-row {
    position: absolute;
    left: 0;
    right: 0;
    top: 232px;
    height: 44px;
    display: flex;
    align-items: center;
  }
  .divider-line {
    flex: 1;
    height: 2px;
    background: var(--accent);
  }
  .person-name {
    padding: 0 14px;
    font-size: 36px;
    letter-spacing: 1.5px;
    white-space: nowrap;
  }
  .contact-list {
    position: absolute;
    left: 0;
    right: 0;
    top: 284px;
    margin: 0;
    padding: 0;
    list-style: none;
    text-align: center;
    font-size: 22px;
    line-height: 30px;
    letter-spacing: 0.5px;
  }
</style>
</head>
<body>
  <div class="business-card">
    <div class="brand-mark">
      <span class="brand-dot"></span>
      <span class="brand-name">Verdelyn</span>
    </div>
    <div class="divider-row">
      <span class="divider-line"></span>
      <span class="person-name">Robert Fairley</span>
      <span class="divider-line"></span>
    </div>
    <ul class="contact-list">
      <li class="contact-phone">(816) 555-2931</li>
      <li class="contact-web">Verdelynkc.com</li>
      <li class="contact-email">robertfairley@verdelynkc.com</li>
      <li class="contact-photo-social">http://snapfolio.com/verdelynkc</li>
      <li class="contact-community-social">neighborly.com/VerdelynGardenandGrounds</li>
    </ul>
  </div>
</body>
</html>
```